New Website Design for PHOVAN.org

We are looking for a new website design for PHOVAN.org. PHOVAN is a non profit home inspector association based in California. Home Inspectors are people that come out and look at a house before it's purchased to let the buyer know of any defects that may exist.
Our site is based on Joomla so if you'll be able to make a Joomla 3 template as well, please let us know (not required, but a bonus).
We would like to see designs that incorporate royal blue, white and chrome into the site as that's our main business colors.
We would like a place for rotating banners though they don't need to be the same size as the current site.
We would like navigation to be easier to manage with menus only across the top (via drop down menus) where we are going to sort out the items currently on the side. Possibly the front page could have a graphic link to separate portals for Realtors, Home Buyers and Inspectors, but that's just one option.
We would like a good mobile design or something that will scale easily to mobile.
The Find an Inspector feature is important and should stand out. The ASK PHOVANr site
Current home page feels a bit busy. Would like to simplify a bit.

```html
<!DOCTYPE html>
<html lang="en">
<head>
<meta charset="utf-8">
<title>PHOVAN – Pacific Home Valuation Network</title>
<link href="https://fonts.googleapis.com/css2?family=Open+Sans:wght@400;600;700&display=swap" rel="stylesheet">
<style>
:root{
  --royal:#3a2b86;
  --royal-dark:#2c206b;
  --ink:#222;
  --muted:#8a8a8a;
  --rule:#e3e3e3;
  --panel:#ececec;
  --footer:#2b2b2b;
  --footer-base:#1f1f1f;
  --footer-text:#b9b9b9;
}
*{box-sizing:border-box;margin:0;padding:0}
html,body{width:858px;height:1200px;overflow:hidden;background:#fff;font-family:"Open Sans",sans-serif;color:var(--ink)}
.page{position:relative;width:858px;height:1200px}
.abs{position:absolute}

.topbar{left:0;top:0;width:858px;height:30px;background:#0d0d0d;border-top:3px solid var(--royal)}
.topbar nav{position:absolute;left:94px;top:8px;font-size:8px;color:#fff;display:flex;gap:14px}
.social{position:absolute;right:92px;top:9px;display:flex;gap:9px}
.social span{width:11px;height:11px;border-radius:50%;background:#fff;display:block}

.brand{left:85px;top:50px;display:flex;align-items:center;gap:8px}
.brand-mark{width:58px;height:58px;border-radius:50%;border:3px solid #c9ccd4;background:#eef0f4}
.brand-name{font-size:12px;font-weight:700;color:var(--royal);line-height:13px;letter-spacing:.3px}

.field{height:20px;border:1px solid #ccc;box-shadow:inset 0 1px 2px rgba(0,0,0,.12);font-size:7px;font-style:italic;color:#666;padding:6px 8px}
.btn{background:var(--royal);color:#fff;font-size:8px;font-weight:600;text-align:center}

.mainnav{left:89px;top:130px;width:681px;height:36px;background:var(--royal);display:flex;align-items:center;padding-left:15px;gap:27.5px;font-size:8px;color:#fff;font-weight:600}
.mainnav svg{position:absolute;right:15px;top:10px}

.hero{left:0;top:166px;width:858px;height:320px;background:linear-gradient(180deg,#8fa36e 0%,#b49a7e 45%,#a58d72 70%,#8c7b6a 100%);border-bottom:3px solid var(--royal)}
.arrow{width:42px;height:42px;border-radius:50%;background:rgba(60,60,60,.75);top:141px}
.caption-title{left:94px;top:186px;width:288px;height:37px;background:#000;color:#fff;font-size:13.5px;font-weight:600;padding:9px 10px}
.caption-text{left:94px;top:223px;width:348px;height:49px;background:var(--royal);color:#fff;font-size:8.5px;line-height:13px;padding:10px 11px}

.section-title{left:0;top:502px;width:858px;text-align:center;font-size:15px;color:#333}
.section-rule{top:514px;height:3px;border-top:1px solid var(--rule);border-bottom:1px solid var(--rule)}

.service{top:542px;width:214px}
.service .thumb{height:126px;border:1px solid #ddd;padding:3px;background:#fff}
.service .thumb div{width:100%;height:100%}
.service h3{margin-top:14px;text-align:center;font-size:10.5px;font-weight:600;color:#222}
.service p{margin-top:9px;font-size:8.5px;line-height:13px;color:var(--muted);padding:0 9px}

.panel{top:778px;height:192px;border:6px solid var(--panel);background:#fff;padding:7px 12px}
.panel h4{font-size:12px;font-weight:700;color:#444}
.links li{list-style:none;font-size:8.5px;color:#333;padding:7px 0;border-bottom:1px solid #eee;width:176px}
.viewall{font-size:10px;color:var(--royal);text-decoration:underline;margin-left:2px;margin-top:5px;display:block}
.event{font-size:7.8px;line-height:13px;color:#444;text-align:justify;padding:7px 0 5px;border-bottom:1px solid #ddd}
.event:last-child{border-bottom:none}
.event a{color:var(--royal);font-weight:600;text-decoration:underline}
.login label{display:block;font-size:8.5px;color:#333;margin-top:10px}
.login .input{height:19px;border:1px solid #ccc;margin-top:4px;width:177px}

.footer{left:0;top:994px;width:858px;height:166px;background:repeating-linear-gradient(45deg,#2d2d2d 0 2px,#282828 2px 4px)}
.footer h5{font-size:11.5px;font-weight:400;color:#fff}
.footer p{font-size:8.3px;line-height:13px;color:var(--footer-text);margin-top:13px}
.base{left:0;top:1160px;width:858px;height:40px;background:var(--footer-base);border-top:1px solid #3a3a3a;text-align:center;font-size:7.5px;color:#999;padding-top:15px}
</style>
</head>
<body>
<div class="page">

  <header class="abs topbar">
    <nav><span>Home</span><span>Events</span><span>FAQ</span><span>Contact</span></nav>
    <div class="social"><span></span><span></span><span></span><span></span><span></span><span></span><span></span></div>
  </header>

  <div class="abs brand">
    <div class="brand-mark"></div>
    <div class="brand-name">PACIFIC HOME VALUATION<br>&nbsp;&nbsp;&nbsp;&nbsp;NETWORK</div>
  </div>

  <div class="abs field" style="left:438px;top:73px;width:110px">Distance..</div>
  <div class="abs field" style="left:558px;top:73px;width:110px">Enter a zip or country</div>
  <div class="abs btn" style="left:675px;top:72px;width:95px;height:20px;line-height:20px">Search for Inspector</div>

  <nav class="abs mainnav">
    <span>HOME</span><span>FIND AN INSPECTOR</span><span>HOME BUYERS &amp; SELLER</span><span>REAL ESTATE AGENTS</span><span>ASK PHOVAN</span><span>INSPECTORS</span><span>CONFERENCES</span>
    <svg width="17" height="17" viewBox="0 0 17 17"><circle cx="7" cy="7" r="5.2" fill="none" stroke="#fff" stroke-width="2"/><line x1="11" y1="11" x2="15.5" y2="15.5" stroke="#fff" stroke-width="2.4" stroke-linecap="round"/></svg>
  </nav>

  <section class="abs hero" role="img" aria-label="Two home inspectors taking notes in front of a brick suburban house">
    <div class="abs arrow" style="left:23px"><svg width="42" height="42"><path d="M24 15 L18 21 L24 27" fill="none" stroke="#fff" stroke-width="2.5"/></svg></div>
    <div class="abs arrow" style="left:794px"><svg width="42" height="42"><path d="M18 15 L24 21 L18 27" fill="none" stroke="#fff" stroke-width="2.5"/></svg></div>
    <div class="abs caption-title">Real Answers from Seasoned Inspectors</div>
    <div class="abs caption-text">Lorem Ipsum is simply dummy text of the printing and typesetting industry is simply dummy text of the printing and typesetting.</div>
  </section>

  <div class="abs section-rule" style="left:94px;width:266px"></div>
  <h2 class="abs section-title">Our Services</h2>
  <div class="abs section-rule" style="left:498px;width:268px"></div>

  <article class="abs service" style="left:94px">
    <div class="thumb"><div role="img" aria-label="Inspector in a hard hat writing on a clipboard by the water" style="background:linear-gradient(180deg,#8bb3d6,#6c8fb0 60%,#b08a5c)"></div></div>
    <h3>PATH TO SUCCESS</h3>
    <p>Lorem Ipsum is simply dummy text of the printing and typesetting industry. Lorem Ipsum has been the industry's standard dummy text</p>
  </article>
  <article class="abs service" style="left:322px">
    <div class="thumb"><div role="img" aria-label="Open book in front of stacked books" style="background:linear-gradient(180deg,#6b4a2a,#9a7448 55%,#d9c29a)"></div></div>
    <h3>EDUCATIONAL PUBLICATIONS</h3>
    <p>Lorem Ipsum is simply dummy text of the printing and typesetting industry. Lorem Ipsum has been the industry's standard dummy text</p>
  </article>
  <article class="abs service" style="left:551px">
    <div class="thumb"><div role="img" aria-label="Figure leaning on a large red question mark" style="background:radial-gradient(circle at 50% 45%,#e8d3d3,#f7f7f7 60%)"></div></div>
    <h3>ASK PHOVAN</h3>
    <p>Lorem Ipsum is simply dummy text of the printing and typesetting industry. Lorem Ipsum has been the industry's standard dummy text</p>
  </article>

  <aside class="abs panel" style="left:90px;width:218px">
    <h4>Home Inspection Software</h4>
    <ul class="links" style="margin-top:3px">
      <li>California Real Estate Inspection Law</li>
      <li>PHOVAN Chapter Meeting Locations</li>
      <li>Standards of Practice</li>
      <li>Code of Ethics</li>
      <li>Education / CEC's</li>
    </ul>
    <span class="viewall">View All</span>
  </aside>

  <aside class="abs panel" style="left:322px;width:218px;padding:7px 14px">
    <h4>Upcoming Events</h4>
    <div class="event">Lorem ipsum dolor sit amet, consectetuer adipiscing elit, sed diam nonummy nibh euismod tincidunt ut. <a>09-08-2013</a></div>
    <div class="event">Lorem ipsum dolor sit amet, consectetuer adipiscing elit, sed diam nonummy nibh euismod tincidunt. <a>09-08-2013</a></div>
    <div class="event">Lorem ipsum dolor sit amet, consectetuer adipiscing elit, sed diam nonummy nibh euismod tincidunt. <a>09-08-2013</a></div>
  </aside>

  <aside class="abs panel login" style="left:555px;width:211px;padding:7px 14px">
    <h4>Inspector Login</h4>
    <p style="font-size:7.8px;color:#444;margin-top:5px">Lorem ipsum dolor sit amet, consectetuer</p>
    <label>Username</label><div class="input"></div>
    <label>Password</label><div class="input"></div>
    <div class="btn" style="width:53px;height:21px;line-height:21px;margin-top:11px">LOGIN</div>
    <a style="position:absolute;right:14px;bottom:9px;font-size:7.5px;color:var(--royal);font-weight:600;text-decoration:underline">Forgot Login?</a>
  </aside>

  <footer class="abs footer">
    <div class="abs" style="left:102px;top:23px"><h5>Popular</h5><p>Inspection FAQs<br>Common Venting of Gas<br>Becoming a Member<br>Education / CECs<br>Affiliate Directory</p></div>
    <div class="abs" style="left:256px;top:23px;width:200px"><h5>Business method</h5><p>Ma quande lingues coalesce, li grammatica del resultant lingue es plu simplic e regulari quam ti del coalescent lingues. Li nov lingua franca va esser plu simplic e regulari quam li existent Europan lingues.</p></div>
    <div class="abs" style="left:494px;top:23px;width:130px"><h5>Get in touch</h5><p>2400 Oak Street Suite 110<br>Riverton CA 90210-0000<br>Hours: M-F, 8:00am - 5:00pm<br>Phone: (800) 555-0142 or<br>(916) 555-0178<br>Fax: (916) 555-0190<br>Webmaster@PHOVAN.ORG</p></div>
    <div class="abs" style="left:654px;top:23px;width:100px"><h5>Who We are</h5><p>Established in 1976, PHOVAN is a non-profit trade association, with chapters located throughout the state. PHOVAN is a member-driven,</p></div>
  </footer>
  <div class="abs base">Copyright © 2013 Phovan. All rights reserved.</div>

</div>
</body>
</html>
```